Crimson Ridge Footrace Co.

We need a website (wordpress) design for a new website that we will be launching. This is for a new trail racing series in Canada.
We recently had a logo designed so want to incorporate the colours of the logo on the website design. Especially the dark blue, green and orange.
Websites that we like for comparison of trail running race themes are:
https://www.mosslinerunning.com/
https://www.bramblestridecup.com/
http://www.quarrypathcircuit.ca/
https://www.cobaltcreekchase.com/
http://www.dunmoorrunningtour.com/

Target Market(s)

Outdoor trail runners

Coding

Coded - Design and coding required

Number of Pages Required

4 page

Font styles to use
Sans Serif

Colors
0255a3
33b8a4
f37122

Requirements
Must have
• There will be a main page with eye catching design noting what we do. Page 2 and 3 will be for each race in the series. Page 1 will be a specific race, and page 2 with be for another race. page 3 and 4 will be for future races that we add so that each race has their own page.
• Our races all take place in the mountains, so using graphics including mountains, rivers, trees is all a requirement for us.
• Our logo is attached, we want to use the colours of the logo in the website design.
Nice to have
• Outdoor theme is a nice to have. We like wood and earth tone colours, and pictures/graphics of runners and mountains and trees.
• There are 4 people involved in our organization. We'd like a photo and brief blurb of each of us, similar to how this website did their layout: https://www.mosslinerunning.com/

```html
<!DOCTYPE html>
<html lang="en">
<head>
<meta charset="utf-8">
<title>Crimson Ridge Footrace Co.</title>
<link href="https://fonts.googleapis.com/css2?family=Montserrat:wght@500;600;700;800&family=Mulish:wght@400;600;700&display=swap" rel="stylesheet">
<style>
:root{
  --earth:#2a211b;
  --earth-deep:#1f1813;
  --orange:#f37122;
  --teal:#33b8a4;
  --blue:#0255a3;
  --blue-deep:#0d3f93;
  --white:#ffffff;
  --muted:#bfb6ad;
  --rule:#5a4c40;
}
*{box-sizing:border-box;margin:0;padding:0}
html,body{width:1200px;height:3704px;overflow:hidden}
body{background:var(--earth);font-family:"Mulish",sans-serif;color:var(--white);position:relative}
.abs{position:absolute}

/* header */
.site-header{left:0;top:0;width:1200px;height:118px;background:var(--earth)}
.brand{left:132px;top:14px;width:160px;height:160px;border-radius:50%;background:var(--earth);display:flex;align-items:center;justify-content:center;text-align:center;z-index:3}
.brand span{font-family:"Montserrat",sans-serif;font-weight:800;font-size:21px;line-height:1.05;color:var(--white);letter-spacing:.5px}
.main-nav{left:406px;top:40px;display:flex;gap:8px;align-items:center}
.main-nav a{font-family:"Montserrat",sans-serif;font-weight:500;font-size:17px;color:var(--white);text-decoration:none;padding:7px 16px}
.main-nav a.active{background:var(--orange)}
.search{left:1070px;top:46px}

/* hero */
.hero{left:0;top:118px;width:1200px;height:648px;background:linear-gradient(180deg,#b7c98e 0%,#6f8a3f 30%,#3f5a22 60%,#2b3a16 100%)}
.hero-title{left:0;top:325px;width:1200px;text-align:center;font-family:"Montserrat",sans-serif;font-weight:800;font-size:74px;letter-spacing:1px}
.hero-sub{left:0;top:440px;width:1200px;text-align:center;font-size:20px;font-weight:600}
.play{left:565px;top:495px}
.arrow{top:420px}

/* section titles */
.section-title{left:0;width:1200px;text-align:center;font-family:"Montserrat",sans-serif;font-weight:600;font-size:35px;letter-spacing:.5px}
.rule{left:104px;width:992px;height:1px;background:var(--rule)}
.rule::after{content:"";position:absolute;left:478px;top:-1px;width:36px;height:3px;background:var(--orange)}

/* events */
.event{width:172px;height:172px;border-radius:50%;background:var(--white);top:1030px;display:flex;align-items:center;justify-content:center;border:4px solid #e6e1dc}
.event.current{border-color:var(--orange)}
.event-caption{top:1236px;width:200px;text-align:center;font-size:13px;line-height:1.75;color:var(--orange);text-transform:uppercase}

/* about */
.about-photo{left:0;top:1408px;width:600px;height:575px;background:linear-gradient(135deg,#f3d9a4 0%,#b9894d 35%,#5c4a2b 70%,#3a2f1c 100%)}
.about-panel{left:600px;top:1408px;width:600px;height:575px;background:linear-gradient(135deg,var(--blue-deep),var(--blue))}
.about-title{left:660px;top:1495px;font-family:"Montserrat",sans-serif;font-weight:600;font-size:35px}
.about-bar{left:660px;top:1553px;width:40px;height:3px;background:var(--white)}
.about-lead{left:660px;top:1590px;width:440px;font-weight:700;font-size:15px;line-height:1.75}
.about-text{left:660px;top:1662px;width:440px;font-size:13px;line-height:2}
.btn-outline{left:656px;top:1840px;width:128px;height:46px;border:2px solid var(--white);font-family:"Montserrat",sans-serif;font-weight:600;font-size:13px;display:flex;align-items:center;justify-content:center}

/* team */
.card{width:492px;height:230px;display:flex}
.card-body{width:282px;padding:24px 16px;height:100%}
.card-body h3{font-family:"Montserrat",sans-serif;font-weight:700;font-size:19px;margin-bottom:8px}
.card-body .role{font-size:12px;margin-bottom:18px}
.card-body p{font-size:12.5px;line-height:1.75}
.card-photo{width:210px;height:100%}
.orange{background:var(--orange)}
.teal{background:var(--teal)}
.photo-a{background:linear-gradient(160deg,#e4e4e4,#9a9a9a)}
.photo-b{background:linear-gradient(160deg,#d9d9d9,#8c8c8c)}

/* contact */
.contact-line{top:2980px;display:flex;align-items:center;gap:18px;font-size:13px;color:var(--muted)}
.contact-line .ring{width:46px;height:46px;border-radius:50%;border:2px solid var(--white);display:flex;align-items:center;justify-content:center}
.field{background:var(--white);color:#9a9a9a;font-size:14px;padding:0 20px;display:flex;align-items:center}
.field.area{align-items:flex-start;padding-top:14px}
.submit{left:882px;top:3260px;width:108px;height:45px;border-radius:23px;background:var(--orange);font-family:"Montserrat",sans-serif;font-weight:700;font-size:14px;display:flex;align-items:center;justify-content:center}

/* footer */
.site-footer{left:0;top:3420px;width:1200px;height:284px;background:var(--earth-deep)}
.social{left:250px;top:3517px;display:flex;gap:8px}
.social span{width:40px;height:40px;border-radius:50%;background:var(--white)}
.footer-nav{left:100px;top:3596px;display:flex;gap:18px;font-size:12px;font-family:"Montserrat",sans-serif}
.footer-nav i{font-style:normal;color:var(--muted)}
.copyright{left:208px;top:3641px;font-size:12px}
.footer-brand{left:918px;top:3500px;width:180px;height:180px;border-radius:50%;background:var(--earth);display:flex;align-items:center;justify-content:center;text-align:center}
.footer-brand span{font-family:"Montserrat",sans-serif;font-weight:800;font-size:22px;line-height:1.05}
</style>
</head>
<body>

<header class="abs site-header">
  <nav class="abs main-nav">
    <a class="active">Home</a><a>About us</a><a>Services</a><a>Team</a><a>Events</a><a>Contact us</a>
  </nav>
  <svg class="abs search" width="22" height="22" viewBox="0 0 22 22"><circle cx="9" cy="9" r="6.5" fill="none" stroke="#fff" stroke-width="2.6"/><line x1="14" y1="14" x2="20" y2="20" stroke="#fff" stroke-width="3" stroke-linecap="round"/></svg>
</header>
<div class="abs brand"><span>CRIMSON<br>RIDGE</span></div>

<section class="abs hero" role="img" aria-label="Sunlit forest trail with tall trees and green undergrowth"></section>
<h1 class="abs hero-title">CRIMSON RIDGE</h1>
<p class="abs hero-sub">Sed ut perspiciatis unde omnis iste natus error sit voluptatem accusantium doloremque</p>
<svg class="abs play" width="70" height="70" viewBox="0 0 70 70"><circle cx="35" cy="35" r="32" fill="none" stroke="#fff" stroke-width="3"/><path d="M27 21 L51 35 L27 49 Z" fill="#fff"/></svg>
<svg class="abs arrow" style="left:40px" width="24" height="44" viewBox="0 0 24 44"><path d="M20 2 L4 22 L20 42" fill="none" stroke="#fff" stroke-width="2.5"/></svg>
<svg class="abs arrow" style="left:1132px" width="24" height="44" viewBox="0 0 24 44"><path d="M4 2 L20 22 L4 42" fill="none" stroke="#fff" stroke-width="2.5"/></svg>

<h2 class="abs section-title" style="top:893px">LATEST EVENTS</h2>
<div class="abs rule" style="top:960px"></div>
<svg class="abs" style="left:42px;top:1130px" width="20" height="38" viewBox="0 0 20 38"><path d="M17 2 L3 19 L17 36" fill="none" stroke="#fff" stroke-width="2.5"/></svg>
<svg class="abs" style="left:1134px;top:1130px" width="20" height="38" viewBox="0 0 20 38"><path d="M3 2 L17 19 L3 36" fill="none" stroke="#fff" stroke-width="2.5"/></svg>
<div class="abs event" style="left:99px"><svg width="70" height="70"><circle cx="35" cy="35" r="30" fill="#3a3a3a"/></svg></div>
<div class="abs event" style="left:304px"><svg width="80" height="80"><circle cx="40" cy="40" r="36" fill="#8a8a8a"/></svg></div>
<div class="abs event current" style="left:514px"><svg width="70" height="70"><circle cx="35" cy="35" r="28" fill="#3a3a3a"/></svg></div>
<div class="abs event" style="left:719px"><svg width="70" height="70"><rect x="8" y="8" width="54" height="54" fill="#2a2a2a"/></svg></div>
<div class="abs event" style="left:927px"><svg width="70" height="70"><rect x="10" y="10" width="50" height="50" fill="#3a3a3a"/></svg></div>
<p class="abs event-caption" style="left:85px">Sed ut perspis unde<br>omnis isnatus</p>
<p class="abs event-caption" style="left:290px">Nemo enim ipsam<br>volem quia</p>
<p class="abs event-caption" style="left:500px">Duis aute irure<br>dolorehe</p>
<p class="abs event-caption" style="left:705px">Excepteur sint occae<br>cat cupidatat</p>
<p class="abs event-caption" style="left:913px">Quis nostrum exer<br>citationem</p>

<div class="abs about-photo" role="img" aria-label="Trail runner on a sunlit forest path"></div>
<section class="abs about-panel"></section>
<h2 class="abs about-title">ABOUT US</h2>
<div class="abs about-bar"></div>
<p class="abs about-lead">Nemo enim ipsam voluptatem quia voluptas sit aspernatur aut odit aut fugit sed quia consequuntur..</p>
<p class="abs about-text">Sed ut perspiciatis unde omnis iste natus error sit voluptatem accusantium doloremque laudantium, totam rem aperiam, eaque ipsa quae ab illo inventore veritatis et quasi architecto beatae vitae dicta sunt explicabo. Nemo enim ipsam voluptatem quia voluptas sit aspernatur aut odit aut fugit, sed quia consequuntur magni dolores eos qui.</p>
<div class="abs btn-outline">READ MORE</div>

<h2 class="abs section-title" style="top:2110px">OUR TEAM</h2>
<div class="abs rule" style="top:2173px"></div>
<article class="abs card" style="left:99px;top:2250px">
  <div class="card-body orange"><h3>John Doe Smith</h3><p class="role">Race Director</p><p>Sed ut perspiciatis unde omnis iste natus error sit voluptatem accusantium doloremque laudantium rem aperiam, eaque ipsa quae ab.</p></div>
  <div class="card-photo photo-a" role="img" aria-label="Portrait photo of team member"></div>
</article>
<article class="abs card" style="left:609px;top:2250px">
  <div class="card-photo photo-b" role="img" aria-label="Portrait photo of team member"></div>
  <div class="card-body teal"><h3>Smith John</h3><p class="role">Race Director</p><p>Sed ut perspiciatis unde omnis iste natus error sit voluptatem accusantium doloremque laudantium rem aperiam, eaque ipsa quae ab.</p></div>
</article>
<article class="abs card" style="left:99px;top:2500px">
  <div class="card-body teal"><h3>Prakvala Dev</h3><p class="role">Race Director</p><p>Sed ut perspiciatis unde omnis iste natus error sit voluptatem accusantium doloremque laudantium rem aperiam, eaque ipsa quae ab.</p></div>
  <div class="card-photo photo-b" role="img" aria-label="Portrait photo of team member"></div>
</article>
<article class="abs card" style="left:609px;top:2500px">
  <div class="card-photo photo-a" role="img" aria-label="Portrait photo of team member"></div>
  <div class="card-body orange"><h3>Jane Nicolson</h3><p class="role">Race Director</p><p>Sed ut perspiciatis unde omnis iste natus error sit voluptatem accusantium doloremque laudantium rem aperiam, eaque ipsa quae ab.</p></div>
</article>

<h2 class="abs section-title" style="top:2863px">GET IN TOUCH</h2>
<div class="abs rule" style="top:2926px"></div>
<div class="abs contact-line" style="left:336px">
  <span class="ring"><svg width="16" height="24" viewBox="0 0 16 24"><rect x="2" y="1" width="12" height="22" rx="2" fill="none" stroke="#fff" stroke-width="2"/><circle cx="8" cy="19" r="1.3" fill="#fff"/></svg></span>
  <span>Phone : 1 888 888 8888</span>
</div>
<div class="abs contact-line" style="left:590px">
  <span class="ring"><svg width="22" height="16" viewBox="0 0 22 16"><rect x="1" y="1" width="20" height="14" rx="2" fill="none" stroke="#fff" stroke-width="2"/><path d="M2 2 L11 9 L20 2" fill="none" stroke="#fff" stroke-width="2"/></svg></span>
  <span>Email : info@companyname.com</span>
</div>
<div class="abs field" style="left:198px;top:3065px;width:387px;height:45px">Enter Name</div>
<div class="abs field" style="left:198px;top:3129px;width:387px;height:45px">Enter Email</div>
<div class="abs field" style="left:198px;top:3193px;width:387px;height:45px">Subject</div>
<div class="abs field area" style="left:603px;top:3065px;width:387px;height:173px">Message</div>
<div class="abs submit">SUBMIT</div>

<footer class="abs site-footer"></footer>
<div class="abs social"><span></span><span></span><span></span><span></span><span></span><span></span></div>
<nav class="abs footer-nav"><span>HOME</span><i>/</i><span>ABOUT US</span><i>/</i><span>SERVICES</span><i>/</i><span>TEAM</span><i>/</i><span>EVENTS</span><i>/</i><span>CONTACT</span></nav>
<p class="abs copyright">© Copyright 2018 Crimson Ridge Footrace Co. All rights reserved &nbsp;|&nbsp; Privacy Policy</p>
<div class="abs footer-brand"><span>CRIMSON<br>RIDGE</span></div>

</body>
</html>
```